Flyer-Design für Heizungsbau
Zielgruppe
Wir sind ein junges, kompetentes und zertifiziertes Fachbetrieb und bieten Beratung, Fachplanung und fachmännische Installation von Wärmepumpen, Klimaanlagen und Lüftungsanlagen. Unsere Zielgruppe sind Eigentümer von Bestandsgebäuden oder Neubauten (hauptsächlich Privatkunden in mittlerem oder höherem Alter), welche eine Heizungssanierung für Heizkostenreduzierung oder neue Heizinstallation (Wärmepumpen), und/oder mehr Komfort bzw. Luftqualität in ihren Zuhause wünschen (Klima und Lüftung).
Aufgabenstellung
Schwerpunkte: 1. Ersparnis an Heizkosten, 2. Wohlgefühl und 3. Klimaschutz

```html
<!DOCTYPE html>
<html lang="de">
<head>
<meta charset="utf-8">
<title>Flyer Heizungsbau – Wickelfalz</title>
<link href="https://fonts.googleapis.com/css2?family=Saira:wght@400;500;600&family=Roboto+Condensed:wght@300;400&display=swap" rel="stylesheet">
<style>
:root{
  --blue:#1d5fa8;
  --blue-light:#3a9ad6;
  --sky:#e2f0fa;
  --orange:#f2ab2f;
  --orange-text:#f0a020;
  --ink:#3b3b3b;
  --muted:#555;
  --frame:#c9c9c9;
}
*{margin:0;padding:0;box-sizing:border-box}
html,body{width:1080px;height:1200px;overflow:hidden;background:#fff}
body{position:relative;font-family:"Roboto Condensed",sans-serif;color:var(--ink)}
.sheet-title{position:absolute;left:45px;top:20px;font-size:9px}
.label{position:absolute;font-size:9px}
.panel{position:absolute;background:#fff;border:1px solid var(--frame);box-shadow:3px 3px 6px rgba(0,0,0,.25);overflow:hidden}
.col{position:absolute;top:0;width:234px;height:495px;overflow:hidden}
.photo{position:absolute;left:0;width:234px}
.sky-band{position:absolute;left:0;width:100%;background:var(--sky)}
.wave{position:absolute;left:0;width:100%}
.brand{display:flex;align-items:center;gap:8px;font-family:"Saira",sans-serif;color:var(--blue-light);font-weight:500}
.brand-dot{border-radius:50%;background:var(--blue)}
.tagline{font-family:"Saira",sans-serif;color:var(--blue);font-size:8px;line-height:11px;white-space:nowrap}
.web{position:absolute;left:0;width:100%;text-align:center;font-family:"Saira",sans-serif;font-weight:600;color:var(--blue);font-size:11px;letter-spacing:.6px}
.h-blue{font-family:"Saira",sans-serif;font-weight:400;color:var(--blue);font-size:15px;line-height:20px}
.h-light{color:var(--blue-light)}
.body{font-size:8.5px;line-height:12px;font-weight:300;color:var(--muted)}
.body p+p{margin-top:10px}
.phone{position:absolute;left:0;width:100%;display:flex;justify-content:center;align-items:center;gap:6px;font-family:"Saira",sans-serif;font-weight:500;color:var(--blue);font-size:11px;letter-spacing:1px}
.address{font-size:8.5px;line-height:12px;font-weight:300;color:var(--muted)}
.feature{position:absolute;display:flex;gap:6px}
.feature-title{font-family:"Saira",sans-serif;font-size:9.5px;color:var(--blue)}
.feature-text{font-size:6.5px;line-height:9px;font-weight:300;color:var(--muted)}
.services{position:absolute;left:26px;top:18px;width:200px}
.services-heading{font-family:"Saira",sans-serif;font-size:12px;color:var(--blue-light)}
.service{display:flex;gap:8px;margin-top:9px}
.service-icon{flex:0 0 20px;height:20px;border-radius:50%;background:var(--blue-light);display:flex;align-items:center;justify-content:center;margin-top:2px}
.service-title{font-family:"Saira",sans-serif;font-size:10px;color:var(--blue-light);line-height:12px}
.service-text{font-size:6.8px;line-height:9px;font-weight:300;color:var(--muted)}
.promise-heading{position:absolute;left:18px;top:416px;font-family:"Saira",sans-serif;font-size:12px;font-weight:500;color:#fff}
.promise{position:absolute;top:440px;display:flex;gap:6px;color:#fff}
.promise-title{font-family:"Saira",sans-serif;font-size:10px}
.promise-text{font-size:6.5px;line-height:9px;font-weight:300}
</style>
</head>
<body>

<div class="sheet-title">Flyer A4 Wickelfalz auf DIN lang Einklapper nach innen</div>

<div class="label" style="left:45px;top:49px">Titel</div>
<div class="label" style="left:316px;top:49px">Einklapper</div>
<div class="label" style="left:556px;top:49px">Rückseite</div>
<div class="label" style="left:856px;top:49px">Titel</div>

<!-- Titel einzeln -->
<section class="panel" style="left:45px;top:63px;width:236px;height:495px">
  <div class="col" style="left:0">
    <div class="brand" style="position:absolute;left:24px;top:80px;font-size:26px"><span class="brand-dot" style="width:22px;height:22px"></span>Luftwerk</div>
    <p class="tagline" style="position:absolute;left:84px;top:121px">Beratung, Planung und fachmännische<br>Installation von Wärmepumpen,<br>Klimaanlagen und Lüftungsanlagen</p>
    <div class="photo" role="img" aria-label="Foto: Frau entspannt im Sessel im hellen Wohnzimmer mit Klimagerät" style="top:199px;height:190px;background:linear-gradient(180deg,#eceae6,#c9c6c0)"></div>
    <div class="sky-band" style="top:385px;height:110px"></div>
    <svg class="wave" style="top:360px" width="236" height="40" viewBox="0 0 236 40"><path d="M0 22 C50 4 90 4 130 18 S200 30 236 12 V40 H0Z" fill="#e2f0fa"/></svg>
    <div class="web" style="top:456px">www.luftwerk-beispiel.de</div>
  </div>
</section>

<!-- Außenseite: Einklapper, Rückseite, Titel -->
<section class="panel" style="left:316px;top:63px;width:702px;height:495px">
  <div class="col" style="left:0">
    <h2 class="h-blue" style="position:absolute;left:22px;top:22px">Ihr Fachbetrieb für<br><span class="h-light">Klimaanlagen und Installation</span></h2>
    <div class="body" style="position:absolute;left:22px;top:80px;width:205px">
      <p>Luftwerk GmbH ist Ihr zuverlässiger Partner im Bereich Klima-, Kälte- und Lüftungstechnik.</p>
      <p>Als zertifiziertes Fachunternehmen bieten wir Ihnen schlüsselfertige Kälte-, Klima- und Lüftungsanlagen von marktführenden Herstellern.</p>
      <p>Von Installations- und Instandhaltungsleistungen bis zu Hygieneinspektionen nach VDI 6022 steht unser zertifiziertes Fachpersonal Ihnen gerne zur Seite.</p>
    </div>
    <div class="photo" role="img" aria-label="Foto: Frau stellt das Thermostat an der Wand ein" style="top:199px;height:190px;background:linear-gradient(160deg,#e6e4e0,#b8b4ad)"></div>
    <div class="sky-band" style="top:385px;height:110px"></div>
    <svg class="wave" style="top:365px" width="234" height="30" viewBox="0 0 234 30"><path d="M0 20 C60 6 120 6 170 18 S220 24 234 16 V30 H0Z" fill="#e2f0fa"/></svg>
    <div class="feature" style="left:38px;top:434px">
      <svg width="16" height="16" viewBox="0 0 16 16"><circle cx="8" cy="8" r="7" fill="none" stroke="#1d5fa8" stroke-width="1.4"/><path d="M4.5 8.2l2.3 2.3 4.6-4.8" stroke="#1d5fa8" stroke-width="1.5" fill="none"/></svg>
      <div><div class="feature-title">Höchste Qualität</div><div class="feature-text">Wir führen jede Arbeit mit höchster<br>Sorgfalt und Qualität durch</div></div>
    </div>
  </div>
  <div class="col" style="left:234px">
    <div class="photo" role="img" aria-label="Foto: Thermostat mit Strickmütze vor türkiser Wand" style="top:0;height:199px;background:linear-gradient(180deg,#a9d8d8,#8fcaca)"></div>
    <p class="body" style="position:absolute;left:32px;top:216px;width:200px">Gerne beantworten wir Ihnen jede Frage und helfen Ihnen mit Ihren Herausforderungen im Bereich der Klima- und Kältetechnik.</p>
    <div class="brand" style="position:absolute;left:52px;top:287px;font-size:15px;gap:5px"><span class="brand-dot" style="width:12px;height:12px"></span>Luftwerk</div>
    <div class="address" style="position:absolute;left:87px;top:308px">Luftwerk GmbH<br>Lindenallee 12<br>12345 Musterstadt<br>Deutschland<br><br>E-Mail: hallo@luftwerk-beispiel.de<br>www.luftwerk-beispiel.de</div>
    <div class="sky-band" style="top:410px;height:85px"></div>
    <svg class="wave" style="top:385px" width="234" height="30" viewBox="0 0 234 30"><path d="M0 20 C60 30 120 30 170 14 S220 8 234 10 V30 H0Z" fill="#e2f0fa"/></svg>
    <div class="phone" style="top:456px"><svg width="12" height="12" viewBox="0 0 12 12"><path d="M2.5 1l2 2.5-1 1.3a7 7 0 0 0 3.7 3.7l1.3-1 2.5 2-1.2 1.5C5.5 11 1 6.5 1 2.2Z" fill="#1d5fa8"/></svg>01234 / 56 78 90</div>
  </div>
  <div class="col" style="left:468px">
    <div class="brand" style="position:absolute;left:24px;top:80px;font-size:26px"><span class="brand-dot" style="width:22px;height:22px"></span>Luftwerk</div>
    <p class="tagline" style="position:absolute;left:84px;top:121px">Beratung, Planung und fachmännische<br>Installation von Wärmepumpen,<br>Klimaanlagen und Lüftungsanlagen</p>
    <div class="photo" role="img" aria-label="Foto: Frau entspannt im Sessel im hellen Wohnzimmer mit Klimagerät" style="top:199px;height:190px;background:linear-gradient(180deg,#eceae6,#c9c6c0)"></div>
    <div class="sky-band" style="top:385px;height:110px"></div>
    <svg class="wave" style="top:360px" width="234" height="40" viewBox="0 0 234 40"><path d="M0 22 C50 4 90 4 130 18 S200 30 234 12 V40 H0Z" fill="#e2f0fa"/></svg>
    <div class="web" style="top:456px">www.luftwerk-beispiel.de</div>
  </div>
</section>

<div class="label" style="left:45px;top:612px">Innenseite 1</div>
<div class="label" style="left:285px;top:612px">Innenseite 2</div>
<div class="label" style="left:585px;top:612px">Einklapper innen</div>
<div class="label" style="left:796px;top:612px">Rückseite</div>

<!-- Innenseiten -->
<section class="panel" style="left:45px;top:627px;width:702px;height:495px">
  <div class="col" style="left:0">
    <h2 class="h-blue" style="position:absolute;left:28px;top:16px;color:var(--orange-text)">Ihr Fachbetrieb für<br>umweltfreundliche,<br>effiziente und sparsame<br><span style="color:var(--blue)">Heizungslösungen</span></h2>
    <p class="body" style="position:absolute;left:28px;top:106px;width:200px">Neben dem Bereich Klima-, Kälte- und Lüftungstechnik bieten wir auch Sanierungen zur Heizkostenreduzierung oder neue Heizinstallationen, wie z.B. Wärmepumpen, und/oder Lösungen für mehr Komfort und Verbesserung der Luftqualität in Ihrem Zuhause (Klima und Lüftung).</p>
  </div>
  <div class="photo" role="img" aria-label="Foto: Tablet mit Energieeffizienz-Anzeige auf einem Tisch" style="left:234px;top:0;height:199px;background:linear-gradient(180deg,#ececec,#d4d4d4)"></div>
  <div class="col" style="left:468px">
    <div class="services">
      <div class="services-heading">Unsere Leistungen</div>
      <div class="service"><span class="service-icon"><svg width="10" height="9" viewBox="0 0 10 9"><path d="M1 1h8v5H4L2 8V6H1Z" fill="#fff"/></svg></span><div><div class="service-title">Beratung</div><div class="service-text">Wir beraten Sie vor Ort und machen auf Ihre Bedürfnisse zugeschnittene Angebote.</div></div></div>
      <div class="service"><span class="service-icon"><svg width="10" height="9" viewBox="0 0 10 9"><path d="M0 1h2l1 4h5l1-3H3" stroke="#fff" fill="none"/><circle cx="4" cy="7.5" r="1" fill="#fff"/><circle cx="7.5" cy="7.5" r="1" fill="#fff"/></svg></span><div><div class="service-title">Verkauf</div><div class="service-text">Bei uns erhalten Sie Ihr Klimagerät zu einem günstigen Preis. Wir verkaufen nur hochwertige Anlagen.</div></div></div>
      <div class="service"><span class="service-icon"><svg width="10" height="9" viewBox="0 0 10 9"><rect x="1" y="3" width="8" height="5" fill="#fff"/><path d="M3.5 3V1.5h3V3" stroke="#fff" fill="none"/></svg></span><div><div class="service-title">Installation</div><div class="service-text">Wir installieren Ihre Klima- oder Heizungsanlage fachmännisch und mit höchster Präzision.</div></div></div>
      <div class="service"><span class="service-icon"><svg width="10" height="10" viewBox="0 0 10 10"><path d="M2 8.5L6 4.5" stroke="#fff" stroke-width="1.6"/><circle cx="7" cy="3" r="2" fill="none" stroke="#fff" stroke-width="1.2"/></svg></span><div><div class="service-title">Wartung</div><div class="service-text">Die notwendigen Wartungen an Ihrer Klima- oder Heizungsanlage führen wir professionell durch.</div></div></div>
    </div>
  </div>
  <div class="photo" role="img" aria-label="Foto: Füße in warmen Socken vor dem Sofa" style="left:0;top:199px;height:296px;background:linear-gradient(180deg,#c8b8a6,#a9998a)"></div>
  <div class="photo" role="img" aria-label="Foto: Wärmepumpe mit Innen- und Außeneinheit" style="left:234px;top:199px;height:296px;background:linear-gradient(180deg,#bdbdbd,#8f8f8f)"></div>
  <div class="photo" role="img" aria-label="Foto: Paar entspannt auf dem Sofa unter dem Klimagerät" style="left:468px;top:199px;height:296px;background:linear-gradient(180deg,#e4e2de,#b9b5ae)"></div>
  <svg class="wave" style="top:355px" width="702" height="140" viewBox="0 0 702 140"><path d="M0 40 C90 20 170 14 260 36 S420 62 520 30 S650 4 702 18 V140 H0Z" fill="#f2ab2f"/></svg>

  <div class="promise-heading">Unser Versprechen</div>
  <div class="promise" style="left:38px">
    <svg width="15" height="15" viewBox="0 0 15 15"><circle cx="7.5" cy="7.5" r="6.5" fill="none" stroke="#fff" stroke-width="1.3"/><path d="M7.5 3.5V7.5L10 9" stroke="#fff" stroke-width="1.3" fill="none"/></svg>
    <div><div class="promise-title">Schnelle Installation</div><div class="promise-text">Garantierte Installation Ihrer Klimaanlage<br>innerhalb von wenigen Wochen</div></div>
  </div>
  <div class="promise" style="left:283px">
    <svg width="16" height="12" viewBox="0 0 16 12"><rect x="1" y="2" width="14" height="8" fill="none" stroke="#fff" stroke-width="1.2"/><circle cx="8" cy="6" r="2" fill="#fff"/></svg>
    <div><div class="promise-title">Faire Preise</div><div class="promise-text">Wir sind von fairen Preisen überzeugt und<br>bieten ein faires Preis-/Leistungsverhältnis</div></div>
  </div>
  <div class="promise" style="left:499px">
    <svg width="16" height="12" viewBox="0 0 16 12"><rect x="1" y="1" width="14" height="10" fill="none" stroke="#fff" stroke-width="1.2"/><path d="M1 4h14" stroke="#fff" stroke-width="1.6"/></svg>
    <div><div class="promise-title">Festpreis</div><div class="promise-text">Alle unsere Angebote sind zum Festpreis und<br>ändern sich durch mehr Aufwand auch nicht.</div></div>
  </div>
</section>

<!-- Rückseite einzeln -->
<section class="panel" style="left:796px;top:627px;width:234px;height:495px">
  <div class="col" style="left:0">
    <div class="photo" role="img" aria-label="Foto: Thermostat mit Strickmütze vor türkiser Wand" style="top:0;height:199px;background:linear-gradient(180deg,#a9d8d8,#8fcaca)"></div>
    <p class="body" style="position:absolute;left:29px;top:216px;width:200px">Gerne beantworten wir Ihnen jede Frage und helfen Ihnen mit Ihren Herausforderungen im Bereich der Klima- und Kältetechnik.</p>
    <div class="brand" style="position:absolute;left:50px;top:287px;font-size:15px;gap:5px"><span class="brand-dot" style="width:12px;height:12px"></span>Luftwerk</div>
    <div class="address" style="position:absolute;left:84px;top:308px">Luftwerk GmbH<br>Lindenallee 12<br>12345 Musterstadt<br>Deutschland<br><br>E-Mail: hallo@luftwerk-beispiel.de<br>www.luftwerk-beispiel.de</div>
    <div class="sky-band" style="top:410px;height:85px"></div>
    <svg class="wave" style="top:385px" width="234" height="30" viewBox="0 0 234 30"><path d="M0 20 C60 30 120 30 170 14 S220 8 234 10 V30 H0Z" fill="#e2f0fa"/></svg>
    <div class="phone" style="top:456px"><svg width="12" height="12" viewBox="0 0 12 12"><path d="M2.5 1l2 2.5-1 1.3a7 7 0 0 0 3.7 3.7l1.3-1 2.5 2-1.2 1.5C5.5 11 1 6.5 1 2.2Z" fill="#1d5fa8"/></svg>01234 / 56 78 90</div>
  </div>
</section>

</body>
</html>
```